Business Card Design

We have recently seen two business cards that caught our attention and think the designs would work for us. We are an accounting firm that serves small businesses in a variety of industries. Attached are the two business card that inspired us along with very rough layouts. We would like to see a professional layout using our company information.

Industry/Entity Type

Accounting

Contact Information for Business Card

Company Name - Marlowe Thistle
Address - 4182 Orlanby Lane, Suite 610, Houston, TX 77093
713-555-0187 - Main
281-555-0342 - Fax

Team Member Names, emails and phone numbers (see attachment)

```html
<!DOCTYPE html>
<html lang="en">
<head>
<meta charset="utf-8">
<title>Marlowe Thistle — Business Card</title>
<link href="https://fonts.googleapis.com/css2?family=Open+Sans:wght@400;600;700&display=swap" rel="stylesheet">
<style>
  :root {
    --backdrop: #e4e4e4;
    --card-light: #fbfbfb;
    --card-shade: #e9e9e9;
    --charcoal: #3a3a3a;
    --band-grey: #a9a9a9;
    --ink: #2b2b2b;
    --muted: #8a8a8a;
    --accent: #d9342b;
    --mark-grey: #c4c4c4;
  }
  * { margin: 0; padding: 0; box-sizing: border-box; }
  html, body { width: 1200px; height: 894px; overflow: hidden; }
  body {
    background: var(--backdrop);
    font-family: "Open Sans", Arial, sans-serif;
    color: var(--ink);
    display: flex;
    align-items: center;
    justify-content: center;
    gap: 40px;
  }
  .card {
    position: relative;
    width: 540px;
    height: 309px;
    background: radial-gradient(ellipse at 60% 45%, var(--card-light) 0%, var(--card-shade) 100%);
    box-shadow: 0 10px 24px rgba(0,0,0,0.18);
    overflow: hidden;
  }
  .edge-band { position: absolute; top: 0; height: 309px; width: 60px; }
  .card-front .edge-band { left: 0; }
  .card-back .edge-band { right: 0; transform: scaleX(-1); }

  .contact-list {
    position: absolute;
    left: 66px;
    top: 42px;
    list-style: none;
    font-size: 14.5px;
    line-height: 24px;
    color: var(--ink);
  }
  .person { position: absolute; left: 66px; top: 160px; }
  .person-name { font-size: 17px; font-weight: 700; }
  .person-title { font-size: 12px; color: var(--muted); margin-top: 1px; }

  .divider {
    position: absolute;
    left: 282px;
    top: 80px;
    width: 1px;
    height: 150px;
    background: linear-gradient(to bottom, transparent, #bdbdbd 30%, #bdbdbd 70%, transparent);
  }
  .brand { display: flex; align-items: center; gap: 9px; }
  .brand-square { background: var(--mark-grey); flex: none; }
  .brand-name { font-weight: 700; color: var(--ink); white-space: nowrap; }

  .card-front .brand { position: absolute; left: 300px; top: 104px; }
  .card-front .brand-square { width: 24px; height: 24px; }
  .card-front .brand-name { font-size: 20px; }

  .address {
    position: absolute;
    left: 300px;
    top: 178px;
    font-size: 12px;
    line-height: 17px;
    width: 220px;
  }
  .website { position: absolute; left: 300px; top: 250px; font-size: 13px; letter-spacing: 0.3px; }
  .website .accent { color: var(--accent); font-weight: 700; }

  .card-back .brand {
    position: absolute;
    left: 0; right: 40px; top: 0; bottom: 0;
    justify-content: center;
  }
  .card-back .brand-square { width: 36px; height: 36px; }
  .card-back .brand-name { font-size: 30px; }
</style>
</head>
<body>

<section class="card card-front" aria-label="Card front">
  <svg class="edge-band" viewBox="0 0 60 309" aria-hidden="true">
    <path fill="var(--band-grey)" d="M0 0 H30 V22 Q30 30 40 32 H48 V150 H40 Q30 152 30 160 V309 H0 Z"/>
    <path fill="var(--charcoal)" d="M0 0 H20 V22 Q20 32 30 34 H40 V148 H30 Q20 150 20 160 V309 H0 Z"/>
    <g fill="#ffffff" stroke="#ffffff">
      <!-- phone handset -->
      <path stroke="none" d="M25 49 q2 -2 4 0 l2 2 q1 1 0 2 l-1 1 q1 3 4 4 l1 -1 q1 -1 2 0 l2 2 q1 2 -1 3 q-3 2 -8 -2 q-5 -5 -5 -11z"/>
      <!-- mobile -->
      <rect x="27" y="70" width="8" height="13" rx="1.5" fill="none" stroke-width="1.6"/>
      <!-- fax -->
      <rect x="25" y="99" width="12" height="8" rx="1" stroke="none"/>
      <rect x="28" y="94" width="6" height="5" fill="none" stroke-width="1.3"/>
      <!-- envelope -->
      <rect x="24.5" y="120" width="13" height="9" fill="none" stroke-width="1.4"/>
      <path d="M24.5 120 L31 125.5 L37.5 120" fill="none" stroke-width="1.4"/>
    </g>
  </svg>

  <ul class="contact-list">
    <li>713-555-0187</li>
    <li>832-555-0219</li>
    <li>281-555-0342</li>
    <li>hello@marlowethistle.com</li>
  </ul>

  <div class="person">
    <p class="person-name">Dorian Vale</p>
    <p class="person-title">President and CEO</p>
  </div>

  <div class="divider"></div>

  <div class="brand">
    <span class="brand-square"></span>
    <span class="brand-name">Marlowe Thistle</span>
  </div>

  <p class="address">4182 Orlanby Lane, Suite 610,<br>Houston, TX 77093</p>
  <p class="website">www.<span class="accent">marlowethistle</span>.com</p>
</section>

<section class="card card-back" aria-label="Card back">
  <svg class="edge-band" viewBox="0 0 60 309" aria-hidden="true">
    <path fill="var(--band-grey)" d="M0 0 H30 V60 Q30 70 40 72 H48 V238 H40 Q30 240 30 250 V309 H0 Z"/>
    <path fill="var(--charcoal)" d="M0 0 H20 V60 Q20 72 30 74 H40 V236 H30 Q20 238 20 250 V309 H0 Z"/>
  </svg>
  <div class="brand">
    <span class="brand-square"></span>
    <span class="brand-name">Marlowe Thistle</span>
  </div>
</section>

</body>
</html>
```